AWESOME RETAILER OF PHONE ACCESSORIES NEEDS AWESOME WEBSITE FROM AWESOME DESIGNER

We currently do not have any website and are looking for one for our new store. We are a retailer who sells tuvaset accessories, speakers, electronics, cables with the best pricing guaranteed. We carry all top name brands including:

TrailShell : http://www.trailshell-example.com/en/

Harecase : http://www.harecase-example.com/

Kelvra : http://www.kelvra-example.com/Default.asp

Davoren : http://www.davoren-example.com/

Tidy Kit : http://www.tidy-kit-example.com/

http://www.glassmantle-example.com/hot-sellers/handset-model-crystl-white.html

http://www.velmarworks-example.com/products/detail.cfm?prodID=2

http://gristcam-example.com/

http://www.quobb-example.com/

We would like to see our logo's used and a website that is trendy and catchy to our demographics. Our demographic is male/female between the ages of 16-45.

Target Market(s)

Male/Femal Ages -16-45

Industry/Entity Type

Electronics

Requirements
Must have
• Must use our logo's and be a catchy fun website keeps the customers eye.
Coupon Tab where customers can print coupons
Products Tab where we can display all of our brands of products
Contact us page
Location Page
FRIENDLOOP/CHIRPNET ACCOUNT TO BE LINKED TO SITE
WEBSITE WILL BE HOSTED BY HOSTWREN-EXAMPLE.COM PLEASE MAKE SURE YOUR DESIGN IS COMPATIBLE WITH THEM.

PLEASE BE SURE TO USE OUR LOGO IN YOUR DESIGN YOU SUBMIT, THEY ARE ATTACHED TO THIS PROJECT
Nice to have
• We would like a slot where a video can be posted from clipvault
Authorized dealer banner
Should not have
• not a dark website but bright and vibrant
Do not use any logos or images that are trademarked by Plumtree.

```html
<!DOCTYPE html>
<html lang="en">
<head>
<meta charset="utf-8">
<title>Voltaro – Phone Accessories</title>
<link rel="stylesheet" href="https://fonts.googleapis.com/css2?family=Source+Sans+3:wght@400;600&display=swap">
<style>
  :root {
    --green: #84b900;
    --green-light: #a2cb3c;
    --ink: #111111;
    --white: #ffffff;
    --tab-dark: #0b0b0f;
    --tab-mid: #5a5a66;
    --tab-light: #cfcff0;
    --globe-dark: #15151c;
    --globe-mid: #6d6d82;
    --globe-light: #d4d4f7;
    --icon-grey: #dcdcdc;
  }
  * { box-sizing: border-box; margin: 0; padding: 0; }
  html, body { width: 1200px; height: 900px; overflow: hidden; background: var(--white); }
  body { font-family: "Source Sans 3", "Myriad Pro", sans-serif; color: var(--ink); }

  .site { position: relative; width: 1200px; height: 900px; }
  .site-frame { position: absolute; inset: 0; }

  .main-nav { position: absolute; inset: 0; pointer-events: none; }
  .nav-tab {
    position: absolute;
    display: flex; align-items: center; justify-content: center;
    height: 60px; width: 130px;
    border: 6px solid var(--white);
    border-radius: 24px;
    background: linear-gradient(100deg, var(--tab-dark) 0%, var(--tab-dark) 12%, var(--tab-mid) 55%, var(--tab-light) 100%);
    color: var(--white);
    font-size: 21px; font-weight: 400;
    text-decoration: none;
    pointer-events: auto;
    padding-bottom: 8px;
  }
  .nav-tab--home     { left: 339px; top: 95px; }
  .nav-tab--products { left: 481px; top: 99px; }
  .nav-tab--location { left: 622px; top: 98px; }
  .nav-tab--contact  { left: 765px; top: 100px; }

  .home-button { position: absolute; left: 111px; top: 216px; width: 188px; height: 188px; }

  .brand {
    position: absolute; left: 417px; top: 338px; width: 400px;
    text-align: center;
  }
  .brand-name { font-size: 60px; font-weight: 400; color: var(--green); line-height: 1; }

  .intro {
    position: absolute; left: 360px; top: 454px; width: 560px;
    font-size: 15.4px; line-height: 19px; color: var(--ink);
  }

  .social-links { position: absolute; right: 288px; top: 733px; display: flex; gap: 10px; }
  .social-link {
    display: flex; align-items: center;
    height: 36px; padding: 0 9px;
    background: var(--white);
    border: 3px solid var(--green);
    border-radius: 8px;
    color: var(--ink); font-size: 13px; font-weight: 600; text-decoration: none;
  }
</style>
</head>
<body>
<div class="site">
  <svg class="site-frame" width="1200" height="900" viewBox="0 0 1200 900" aria-hidden="true">
    <defs>
      <linearGradient id="frame-gloss" x1="0" y1="0" x2="0" y2="1">
        <stop offset="0" stop-color="var(--green-light)"/>
        <stop offset="1" stop-color="var(--green-light)" stop-opacity="0.85"/>
      </linearGradient>
      <clipPath id="frame-clip">
        <rect x="160" y="32" width="905" height="813" rx="92"/>
      </clipPath>
    </defs>
    <rect class="frame-band" x="160" y="32" width="905" height="813" rx="92" fill="var(--green)"/>
    <path class="frame-gloss" clip-path="url(#frame-clip)" d="M150 20 L1080 20 L1080 70 Q620 48 150 70 Z" fill="url(#frame-gloss)"/>
    <path class="content-area" fill="var(--white)"
      d="M100 182 Q190 170 262 181 C272 142 302 123 345 122 L900 122 C932 124 950 142 962 167 Q1015 160 1080 165 L1080 713 Q1015 719 962 711 C944 741 915 755 880 755 L330 755 C290 755 261 725 260 690 L260 441 Q190 432 100 440 Z"/>
  </svg>

  <nav class="main-nav">
    <a class="nav-tab nav-tab--home" href="#">Home</a>
    <a class="nav-tab nav-tab--products" href="#">Products</a>
    <a class="nav-tab nav-tab--location" href="#">Location</a>
    <a class="nav-tab nav-tab--contact" href="#">Contact</a>
  </nav>

  <svg class="home-button" viewBox="0 0 188 188" role="img" aria-label="Home">
    <defs>
      <radialGradient id="globe-fill" cx="0.52" cy="0.95" r="0.95">
        <stop offset="0" stop-color="var(--globe-light)"/>
        <stop offset="0.45" stop-color="var(--globe-mid)"/>
        <stop offset="1" stop-color="var(--globe-dark)"/>
      </radialGradient>
    </defs>
    <circle cx="94" cy="94" r="93" fill="url(#globe-fill)"/>
    <ellipse cx="94" cy="48" rx="62" ry="40" fill="#9a9aa0" opacity="0.75"/>
    <path d="M54 94 L94 60 L134 94 L122 94 L122 130 L108 130 L108 108 L80 108 L80 130 L66 130 L66 94 Z" fill="var(--icon-grey)"/>
  </svg>

  <div class="brand">
    <span class="brand-name">Voltaro</span>
  </div>

  <p class="intro">Our company sells, tuvaset accessories, cables, small electronics, headphones. Our company sells, tuvaset accessories, cables, small electronics, headphones. Our company sells, tuvaset accessories, cables, small electronics, headphones. Our company sells, tuvaset accessories, cables, small electronics, headphones.</p>

  <div class="social-links">
    <a class="social-link" href="#">Friendloop</a>
    <a class="social-link" href="#">Chirpnet</a>
  </div>
</div>
</body>
</html>
```